Brightfen Business Card Redesign & Logo Update

We need to update our business cards to something more modern and fresh. Brightfen can provide the current color schemes and old design examples, but welcome creativity in helping us with this redesign. PLEASE NOTE that we no longer utilize the "tree" and/or "leaf" imagery in our branding. If able would apprecaite an update on the quality of our "words only" logo in Ai. / PNG formats too.

Target Market(s)

Investors, landowners, corporate partners, contractors

Industry/Entity Type

Environmental Restoration & Conservation

Contact Information for Business Card

Logo, persons name, title, mailing address, phone and email, website url

Font styles to use
Other font styles liked:
• Merriweather

Requirements
Nice to have
• Logo, persons name, title, mailing address, phone and email, website url, but open to ideams
Should not have
• No all back backgrounds

```html
<!DOCTYPE html>
<html lang="en">
<head>
<meta charset="utf-8">
<title>Brightfen Business Card</title>
<link rel="stylesheet" href="https://fonts.googleapis.com/css2?family=Oswald:wght@600;700&family=Montserrat:wght@400;500;600&display=swap">
<style>
  :root {
    --forest: #025020;
    --forest-mid: #0e6a2f;
    --orange: #f18a1c;
    --white: #ffffff;
    --backdrop: #3a3a3a;
  }
  * { box-sizing: border-box; margin: 0; padding: 0; }
  html, body {
    width: 1200px; height: 1200px; overflow: hidden;
    background: var(--backdrop);
  }
  .canvas {
    position: relative; width: 1200px; height: 1200px;
    display: flex; flex-direction: column; align-items: center; justify-content: center; gap: 60px;
  }
  .card {
    position: relative; width: 840px; height: 480px;
    border-radius: 36px; overflow: hidden;
    box-shadow: 0 18px 40px rgba(0,0,0,.45);
  }

  /* Front */
  .card-front { display: flex; background: var(--white); }
  .contact-panel {
    width: 380px; height: 100%;
    background: var(--forest);
    padding: 150px 0 0 48px;
    color: var(--white);
    font-family: "Montserrat", sans-serif;
  }
  .panel-stripe { width: 14px; height: 100%; background: var(--orange); }
  .brand-panel {
    flex: 1; display: flex; flex-direction: column; justify-content: center; align-items: center;
    padding-bottom: 30px;
  }
  .person { border-left: 6px solid var(--orange); padding-left: 12px; margin-bottom: 26px; }
  .person-name {
    font-size: 40px; font-weight: 500; color: var(--orange); letter-spacing: 1px; line-height: 1;
  }
  .person-title { font-size: 17px; font-weight: 500; letter-spacing: 1px; margin-top: 4px; }
  .contact-list { list-style: none; }
  .contact-list li {
    display: flex; align-items: flex-start; gap: 10px;
    font-size: 18px; line-height: 1.2; margin-bottom: 6px;
  }
  .contact-list svg { width: 20px; height: 20px; flex: none; margin-top: 1px; }

  .wordmark {
    font-family: "Oswald", sans-serif; font-weight: 700;
    letter-spacing: 1px; line-height: 0.95; text-transform: uppercase;
  }
  .tagline {
    font-family: "Oswald", sans-serif; font-weight: 600;
    text-transform: uppercase; letter-spacing: 0.5px;
  }
  .brand-panel .wordmark { font-size: 78px; color: var(--forest-mid); }
  .brand-panel .tagline { font-size: 20px; color: var(--forest-mid); margin-top: 4px; }

  /* Back */
  .card-back {
    background: linear-gradient(115deg, var(--forest) 0%, var(--forest) 40%, #1b6a38 52%, var(--forest) 64%, var(--forest) 100%);
    display: flex; flex-direction: column; align-items: center; justify-content: center;
    padding-bottom: 50px;
  }
  .card-back .wordmark { font-size: 150px; color: var(--white); }
  .card-back .tagline { font-size: 38px; color: var(--white); margin-top: 6px; }
  .back-bar {
    position: absolute; left: 380px; right: 110px; bottom: 40px;
    height: 20px; background: var(--orange);
  }
</style>
</head>
<body>
<main class="canvas">

  <section class="card card-front" aria-label="Business card front">
    <div class="contact-panel">
      <div class="person">
        <p class="person-name">JOHN DOE</p>
        <p class="person-title">POSITION</p>
      </div>
      <ul class="contact-list">
        <li>
          <svg viewBox="0 0 24 24" aria-hidden="true"><path fill="#f18a1c" d="M6.6 10.8a15.1 15.1 0 0 0 6.6 6.6l2.2-2.2a1 1 0 0 1 1-.25 11.4 11.4 0 0 0 3.6.57 1 1 0 0 1 1 1V20a1 1 0 0 1-1 1A17 17 0 0 1 3 4a1 1 0 0 1 1-1h3.5a1 1 0 0 1 1 1c0 1.25.2 2.45.57 3.57a1 1 0 0 1-.25 1z"/></svg>
          <span>(000) 000 0000</span>
        </li>
        <li>
          <svg viewBox="0 0 24 24" aria-hidden="true"><rect x="2" y="5" width="20" height="14" fill="#f18a1c"/><path d="M2 5l10 8 10-8" fill="none" stroke="#025020" stroke-width="1.8"/></svg>
          <span>email@yourwebsite.com</span>
        </li>
        <li>
          <svg viewBox="0 0 24 24" aria-hidden="true"><g fill="none" stroke="#f18a1c" stroke-width="1.8"><circle cx="12" cy="12" r="9"/><ellipse cx="12" cy="12" rx="4" ry="9"/><path d="M3 12h18M5 7h14M5 17h14"/></g></svg>
          <span>www.yourwebsite.com</span>
        </li>
        <li>
          <svg viewBox="0 0 24 24" aria-hidden="true"><path fill="#f18a1c" d="M12 2a7 7 0 0 0-7 7c0 5 7 13 7 13s7-8 7-13a7 7 0 0 0-7-7zm0 9.5A2.5 2.5 0 1 1 12 6.5a2.5 2.5 0 0 1 0 5z"/></svg>
          <span>123 Name Street, 000<br>Your City, 00000-000</span>
        </li>
      </ul>
    </div>
    <div class="panel-stripe"></div>
    <div class="brand-panel">
      <p class="wordmark">Brightfen</p>
      <p class="tagline">Environmental Credit Company</p>
    </div>
  </section>

  <section class="card card-back" aria-label="Business card back">
    <p class="wordmark">Brightfen</p>
    <p class="tagline">Environmental Credit Company</p>
    <div class="back-bar"></div>
  </section>

</main>
</body>
</html>
```